Redesign for a start up airline technology. The website is quelbrion.com.

I need a PowerPoint template that complements our website. I can provide our current template as a starting point.

```html
<!DOCTYPE html>
<html lang="en">
<head>
<meta charset="utf-8">
<title>Quelbrion Presentation Template</title>
<link rel="stylesheet" href="https://fonts.googleapis.com/css2?family=Poppins:wght@300;400;500;600;700;800&display=swap">
<style>
:root{
  --blue:#1a94e6;
  --navy:#2a3b9c;
  --green:#6cb33e;
  --green-light:#9cd04a;
  --ink:#1b1b1b;
  --body:#4a4a4a;
  --canvas:#ffffff;
  --slide:#ffffff;
  --photo-dark:#0d2a5a;
}
*{box-sizing:border-box;margin:0;padding:0}
html,body{width:1200px;height:823px;overflow:hidden;background:var(--canvas)}
body{position:relative;font-family:'Poppins',sans-serif;color:var(--ink)}
.slide{position:absolute;width:352px;height:198px;background:var(--slide);overflow:hidden;box-shadow:0 3px 14px rgba(0,0,0,.12)}
.c1{left:34px}.c2{left:427px}.c3{left:821px}
.r1{top:59px}.r2{top:315px}.r3{top:572px}

/* brand mark */
.brand{position:absolute;display:flex;align-items:center;gap:3px;font-weight:700;color:var(--navy);line-height:1}
.brand::before{content:"";display:block;border-radius:50%;background:var(--blue)}
.brand-corner{top:9px;right:8px;font-size:9px}
.brand-corner::before{width:6px;height:6px}

/* footer */
.footer{position:absolute;left:0;right:0;bottom:3px;height:12px;display:flex;align-items:center;justify-content:space-between}
.footer-url{height:12px;width:67px;background:var(--blue);color:#fff;font-size:4.2px;display:flex;align-items:center;gap:5px;padding-left:7px}
.footer-url svg{width:6px;height:6px}
.footer-copy{font-size:4.2px;color:var(--body)}
.footer-page{height:12px;width:23px;background:var(--blue);color:#fff;font-size:4px;display:flex;align-items:center;justify-content:center}

/* section title */
.title{position:absolute;font-weight:700;font-size:10px;color:var(--ink);padding-left:6px;border-left:1px solid var(--ink);line-height:1.05;white-space:nowrap}
.title-center{left:50%;transform:translateX(-50%)}
.para{font-size:4.2px;line-height:1.75;color:var(--body);text-align:justify}

/* cover */
.cover .brand{top:22px;left:50%;transform:translateX(-50%);font-size:26px;gap:6px}
.cover .brand::before{width:14px;height:14px}
.cover-heading{position:absolute;top:89px;width:100%;text-align:center;font-weight:800;font-size:16.5px;letter-spacing:.3px}
.cover-sub{position:absolute;top:113px;width:100%;text-align:center;font-weight:300;font-size:9.8px;color:#333}
.cover-contacts{position:absolute;top:168px;left:33px;right:40px;display:flex;justify-content:space-between;align-items:center}
.contact{display:flex;align-items:center;gap:3px;font-size:6.4px;color:#222}
.contact svg{width:10px;height:10px}
.contact-sep{width:.6px;height:14px;background:#ccc}
.cover-rule{position:absolute;top:183px;left:0;right:0;height:.6px;background:#ddd}
.cover-copy{position:absolute;top:187px;width:100%;text-align:center;font-size:4.3px;color:#333}

/* agenda */
.agenda-item{position:absolute;width:126px;height:16px;border-radius:8px;color:#fff;font-size:4.3px;font-weight:500;display:flex;align-items:center;justify-content:space-between;padding:0 10px 0 9px;box-shadow:0 2px 3px rgba(0,0,0,.18)}
.agenda-blue{left:43px;background:linear-gradient(90deg,var(--navy),var(--blue))}
.agenda-green{left:184px;background:linear-gradient(90deg,var(--green),var(--green-light))}
.agenda-item b{font-weight:600;font-size:4.6px}

/* photo placeholders */
.photo{position:absolute;border-radius:50%}
.about-photo{left:39px;top:34px;width:132px;height:132px;border:3px solid var(--blue);background:radial-gradient(circle at 55% 55%,#e0a35a,#8a4a22 45%,#2d1a12 80%)}
.about-text{position:absolute;left:191px;top:94px;width:127px}

.ph-main{left:68px;top:64px;width:100px;height:100px;background:radial-gradient(circle at 50% 50%,#c7ced8,#5a6f8e 55%,#223a66)}
.ph-a{left:81px;top:10px;width:46px;height:46px;background:radial-gradient(circle,#6a6f78,#243042)}
.ph-b{left:51px;top:48px;width:31px;height:31px;background:radial-gradient(circle,#d07a3a,#3a2a2a)}
.ph-c{left:134px;top:48px;width:16px;height:16px;background:radial-gradient(circle,#e08a3a,#33394a)}
.ph-d{left:77px;top:162px;width:8px;height:8px;background:#2d3f66}
.dot{position:absolute;width:2.4px;height:2.4px;border-radius:50%;background:var(--navy);left:159px;top:148px}
.s4-text{position:absolute;left:188px;top:76px;width:127px}
.s4-text .para+.para{margin-top:4px}

/* features grid */
.intro{position:absolute;left:47px;right:47px;top:36px;text-align:center;font-size:4.3px;line-height:1.8;color:var(--body)}
.feature{position:absolute;width:86px;border-left:.6px solid var(--green);padding-left:5px}
.feature-head{display:flex;gap:3px;align-items:flex-start}
.feature-num{font-size:11px;font-weight:600;color:var(--blue);line-height:1}
.feature-name{font-size:3.9px;font-weight:600;line-height:1.3;margin-top:1px;color:var(--ink)}
.feature .para{margin-top:4px;font-size:3.3px;line-height:1.7}

/* cycle diagram */
.cycle-label{position:absolute;width:104px}
.cycle-label h4{font-size:4.3px;font-weight:600;line-height:1.35;color:var(--ink)}
.cycle-label p{font-size:3.2px;line-height:1.45;color:var(--body);margin-top:2px}
.right-al{text-align:right}
.center-al{text-align:center}
.cycle svg{position:absolute;left:0;top:0}
.cycle .brand{left:50%;top:84px;transform:translateX(-50%) translateX(1px);font-size:7.5px}
.cycle .brand::before{width:4px;height:4px}

/* section divider */
.divider-photo{position:absolute;inset:0;background:radial-gradient(ellipse at 70% 45%,#2f6fd0 0%,#13408a 35%,var(--photo-dark) 70%,#081a3a 100%)}
.divider-title{position:absolute;left:22px;top:81px;font-size:14px;font-weight:700;color:#fff;border-left:1px solid #fff;padding-left:6px;line-height:1.05}
.divider-sub{position:absolute;left:23px;top:100px;width:170px;font-size:5.2px;line-height:1.5;color:#fff}

/* bullets */
.bullets{position:absolute;list-style:none}
.bullets li{position:relative;padding-left:7px;font-size:4.3px;line-height:1.72;color:var(--body)}
.bullets li::before{content:"";position:absolute;left:0;top:2.6px;width:2.6px;height:2.6px;border-radius:50%;background:var(--blue)}
.bullets-wide{left:33px;right:33px;top:41px}
.bullets-wide li{margin-bottom:4.6px}
.bullets-left{left:19px;top:35px;width:155px}
.bullets-right{left:198px;top:35px;width:130px}
.bullets-left li,.bullets-right li{margin-bottom:4.4px;text-align:justify}
.col-rule{position:absolute;left:185px;top:36px;height:138px;width:.6px;background:#ccc}
</style>
</head>
<body>

<!-- Cover -->
<section class="slide cover c1 r1">
  <div class="brand">Quelbrion</div>
  <h1 class="cover-heading">HEADING ONE</h1>
  <p class="cover-sub">Ckaseoi Rasek Uasencase Pasersea</p>
  <div class="cover-contacts">
    <span class="contact"><svg viewBox="0 0 20 20"><circle cx="10" cy="10" r="9" fill="none" stroke="#999" stroke-width="1"/><circle cx="10" cy="10" r="6" fill="var(--green)"/><path d="M4 10h12M10 4v12" stroke="#fff" stroke-width="1"/></svg>www.quelbrion.com</span>
    <span class="contact-sep"></span>
    <span class="contact"><svg viewBox="0 0 20 20"><circle cx="10" cy="10" r="9" fill="none" stroke="#999" stroke-width="1"/><circle cx="10" cy="10" r="6" fill="var(--green)"/><rect x="6.5" y="8" width="7" height="5" fill="none" stroke="#fff" stroke-width="1"/><path d="M6.5 8l3.5 3 3.5-3" fill="none" stroke="#fff" stroke-width="1"/></svg>info@quelbrion.com</span>
    <span class="contact-sep"></span>
    <span class="contact"><svg viewBox="0 0 20 20"><circle cx="10" cy="10" r="9" fill="none" stroke="#999" stroke-width="1"/><path d="M7 6l2 0 1 2.5-1.2 1a6 6 0 0 0 2.7 2.7l1-1.2 2.5 1v2a1 1 0 0 1-1 1A8 8 0 0 1 6 7a1 1 0 0 1 1-1z" fill="var(--green)"/></svg>+1 555 014 0199</span>
  </div>
  <div class="cover-rule"></div>
  <p class="cover-copy">© 2024. ALL Rights Reserved.</p>
</section>

<!-- Agenda -->
<section class="slide c2 r1">
  <h2 class="title" style="left:155px;top:13px">Agenda</h2>
  <div class="brand brand-corner">Quelbrion</div>
  <div class="agenda-item agenda-blue" style="top:35px"><span>01.&nbsp; Perspiciatis Unde</span><b>02</b></div>
  <div class="agenda-item agenda-blue" style="top:58px"><span>02.&nbsp; Perspiciatis Unde</span><b>03</b></div>
  <div class="agenda-item agenda-blue" style="top:81px"><span>03.&nbsp; Perspiciatis Unde</span><b>04</b></div>
  <div class="agenda-item agenda-blue" style="top:104px"><span>04.&nbsp; Perspiciatis Unde</span><b>05</b></div>
  <div class="agenda-item agenda-blue" style="top:127px"><span>05.&nbsp; Perspiciatis Unde</span><b>06</b></div>
  <div class="agenda-item agenda-blue" style="top:150px"><span>06.&nbsp; Perspiciatis Unde</span><b>07</b></div>
  <div class="agenda-item agenda-green" style="top:35px"><span>01.&nbsp; Perspiciatis Unde</span><b>02</b></div>
  <div class="agenda-item agenda-green" style="top:58px"><span>02.&nbsp; Perspiciatis Unde</span><b>03</b></div>
  <div class="agenda-item agenda-green" style="top:81px"><span>03.&nbsp; Perspiciatis Unde</span><b>04</b></div>
  <div class="agenda-item agenda-green" style="top:104px"><span>04.&nbsp; Perspiciatis Unde</span><b>05</b></div>
  <div class="agenda-item agenda-green" style="top:127px"><span>05.&nbsp; Perspiciatis Unde</span><b>06</b></div>
  <div class="agenda-item agenda-green" style="top:150px"><span>06.&nbsp; Perspiciatis Unde</span><b>07</b></div>
  <footer class="footer"><span class="footer-url"><svg viewBox="0 0 12 12"><circle cx="6" cy="6" r="5" fill="none" stroke="#fff" stroke-width="1"/><path d="M1 6h10M6 1c2.5 3 2.5 7 0 10M6 1c-2.5 3-2.5 7 0 10" fill="none" stroke="#fff" stroke-width=".8"/></svg>www.quelbrion.com</span><span class="footer-copy">© 2024. ALL Rights Reserved.</span><span class="footer-page">Page 02</span></footer>
</section>

<!-- About -->
<section class="slide c3 r1">
  <div class="brand brand-corner">Quelbrion</div>
  <div class="photo about-photo" role="img" aria-label="Close-up photo of a jet engine fan with glowing copper blades"></div>
  <h2 class="title" style="left:189px;top:73px">About Us</h2>
  <p class="para about-text">Omnis isasdte natus errorsit voluseptatem accusantium doloremque laudantium, totasem rsem aperiam, eaque ipsa quae seab illo inventore veritatis et quasi architecto beatae vitae dicta sunt explicabo. Nemo enim ipsam voluptatem quia voluptas sit aspernatur aut odit.</p>
  <footer class="footer"><span class="footer-url"><svg viewBox="0 0 12 12"><circle cx="6" cy="6" r="5" fill="none" stroke="#fff" stroke-width="1"/><path d="M1 6h10M6 1c2.5 3 2.5 7 0 10M6 1c-2.5 3-2.5 7 0 10" fill="none" stroke="#fff" stroke-width=".8"/></svg>www.quelbrion.com</span><span class="footer-copy">© 2024. ALL Rights Reserved.</span><span class="footer-page">Page 03</span></footer>
</section>

<!-- Text with photo cluster -->
<section class="slide c1 r2">
  <div class="brand brand-corner">Quelbrion</div>
  <div class="photo ph-a" role="img" aria-label="Photo of a technician servicing an engine"></div>
  <div class="photo ph-b" role="img" aria-label="Photo of engineering work with orange safety gear"></div>
  <div class="photo ph-c" role="img" aria-label="Small photo of engine maintenance"></div>
  <div class="photo ph-main" role="img" aria-label="Photo of precision gear components on technical plans"></div>
  <div class="photo ph-d" role="img" aria-label="Tiny photo of a mechanical part"></div>
  <span class="dot"></span>
  <h2 class="title" style="left:188px;top:55px">Kcas saeicas sesaec</h2>
  <div class="s4-text">
    <p class="para">Omnis isasdte natus errorsit voluseptatem accusantium doloremque laudantium, totasem rsem aperiam, eaque ipsa quae seab illo inventore veritatis et quasi architecto beatae vitae dicta sunt explicabo. Nemo enim ipsam voluptatem quia voluptas sit aspernatur aut odit.</p>
    <p class="para">Kasesdte naasestus errorsit voluseptatem accusantium doloremque laudantium, totasem rsem aperiam, eaque ipsa quae seab illo inventore veritatis et quasi architecto beatae vitae dicta sunt explicabo. Nemo enim ipsam voluptatem quia voluptas sit aspernatur aut odit.</p>
  </div>
  <footer class="footer"><span class="footer-url"><svg viewBox="0 0 12 12"><circle cx="6" cy="6" r="5" fill="none" stroke="#fff" stroke-width="1"/><path d="M1 6h10M6 1c2.5 3 2.5 7 0 10M6 1c-2.5 3-2.5 7 0 10" fill="none" stroke="#fff" stroke-width=".8"/></svg>www.quelbrion.com</span><span class="footer-copy">© 2024. ALL Rights Reserved.</span><span class="footer-page">Page 04</span></footer>
</section>

<!-- Six features -->
<section class="slide c2 r2">
  <div class="brand brand-corner">Quelbrion</div>
  <h2 class="title title-center" style="top:15px">Kcas saeicas sesaec</h2>
  <p class="intro">Omnis isasdte natus errorsit voluseptatem accusantium doloremque laudantium, totasem rsem aperiam, eaque ipsa quae seab illo inventore veritatis et quasi architecto beatae vitae dicta sunt explicabo. Nemo enim ipsam voluptatem quia voluptas sit aspernatur aut odit.</p>
  <div class="feature" style="left:27px;top:75px"><div class="feature-head"><span class="feature-num">1.</span><span class="feature-name">VOLUPTATEM ACCUSANTIUM DOLOREMQUE LAUD.</span></div><p class="para">Werspiciatis aseeunde omnis iste natus error sitvolasuptate masease accusantium dolorem quelaudtium, totam rem aperiam.</p></div>
  <div class="feature" style="left:135px;top:75px"><div class="feature-head"><span class="feature-num">2.</span><span class="feature-name">VOLUPTATEM ACCUSANTIUM DOLOREMQUE LAUD.</span></div><p class="para">Werspiciatis aseeunde omnis iste natus error sitvolasuptate masease accusantium dolorem quelaudtium, totam rem aperiam.</p></div>
  <div class="feature" style="left:243px;top:75px"><div class="feature-head"><span class="feature-num">3.</span><span class="feature-name">VOLUPTATEM ACCUSANTIUM DOLOREMQUE LAUD.</span></div><p class="para">Werspiciatis aseeunde omnis iste natus error sitvolasuptate masease accusantium dolorem quelaudtium, totam rem aperiam.</p></div>
  <div class="feature" style="left:27px;top:125px"><div class="feature-head"><span class="feature-num">4.</span><span class="feature-name">VOLUPTATEM ACCUSANTIUM DOLOREMQUE LAUD.</span></div><p class="para">Werspiciatis aseeunde omnis iste natus error sitvolasuptate masease accusantium dolorem quelaudtium, totam rem aperiam.</p></div>
  <div class="feature" style="left:135px;top:125px"><div class="feature-head"><span class="feature-num">5.</span><span class="feature-name">VOLUPTATEM ACCUSANTIUM DOLOREMQUE LAUD.</span></div><p class="para">Werspiciatis aseeunde omnis iste natus error sitvolasuptate masease accusantium dolorem quelaudtium, totam rem aperiam.</p></div>
  <div class="feature" style="left:243px;top:125px"><div class="feature-head"><span class="feature-num">6.</span><span class="feature-name">VOLUPTATEM ACCUSANTIUM DOLOREMQUE LAUD.</span></div><p class="para">Werspiciatis aseeunde omnis iste natus error sitvolasuptate masease accusantium dolorem quelaudtium, totam rem aperiam.</p></div>
  <footer class="footer"><span class="footer-url"><svg viewBox="0 0 12 12"><circle cx="6" cy="6" r="5" fill="none" stroke="#fff" stroke-width="1"/><path d="M1 6h10M6 1c2.5 3 2.5 7 0 10M6 1c-2.5 3-2.5 7 0 10" fill="none" stroke="#fff" stroke-width=".8"/></svg>www.quelbrion.com</span><span class="footer-copy">© 2024. ALL Rights Reserved.</span><span class="footer-page">Page 05</span></footer>
</section>

<!-- Cycle diagram -->
<section class="slide cycle c3 r2">
  <svg width="352" height="198" viewBox="0 0 352 198">
    <path d="M133 47 A58 58 0 0 0 122 110 M127 110 A58 58 0 0 0 222 144 M222 144 A58 58 0 0 0 231 110 M231 110 A58 58 0 0 0 218 47" fill="none" stroke="#b8bcc4" stroke-width=".6"/>
    <circle cx="177" cy="89" r="40" fill="none" stroke="var(--blue)" stroke-width="1.3"/>
    <circle cx="177" cy="89" r="36" fill="none" stroke="var(--blue)" stroke-width=".5"/>
    <circle cx="133" cy="47" r="2.6" fill="#fff" stroke="var(--blue)" stroke-width=".7"/>
    <circle cx="218" cy="47" r="2.6" fill="#fff" stroke="var(--blue)" stroke-width=".7"/>
    <circle cx="122" cy="110" r="2.6" fill="#fff" stroke="var(--blue)" stroke-width=".7"/>
    <circle cx="231" cy="110" r="2.6" fill="#fff" stroke="var(--blue)" stroke-width=".7"/>
    <circle cx="177" cy="146" r="2.6" fill="#fff" stroke="var(--blue)" stroke-width=".7"/>
  </svg>
  <div class="brand brand-corner">Quelbrion</div>
  <h2 class="title title-center" style="top:15px">Kcas saeicas sesaec</h2>
  <div class="brand">Quelbrion</div>
  <div class="cycle-label right-al" style="left:12px;top:41px"><h4>Faerspiciatis unde omnis iste natus error sit voluptatem</h4><p>Werspiciatis aseeunde omnis iste natus error sitvolasuptate masease accusantium dolorem quelaudtium, totam rem aperiam.</p></div>
  <div class="cycle-label" style="left:230px;top:41px"><h4>Faerspiciatis unde omnis iste natus error sit voluptatem</h4><p style="padding-left:9px">Werspiciatis aseeunde omnis iste natus error sitvolasuptate masease accusantium dolorem quelaudtium, totam rem aperiam.</p></div>
  <div class="cycle-label right-al" style="left:12px;top:104px"><h4>Faerspiciatis unde omnis iste natus error sit voluptatem</h4><p>Werspiciatis aseeunde omnis iste natus error sitvolasuptate masease accusantium dolorem quelaudtium, totam rem aperiam.</p></div>
  <div class="cycle-label" style="left:237px;top:104px"><h4>Faerspiciatis unde omnis iste natus error sit voluptatem</h4><p style="padding-left:5px">Werspiciatis aseeunde omnis iste natus error sitvolasuptate masease accusantium dolorem quelaudtium, totam rem aperiam.</p></div>
  <div class="cycle-label center-al" style="left:102px;top:154px;width:150px"><h4>Faerspiciatis unde omnis iste natus error sit voluptatem</h4><p>Werspiciatis aseeunde omnis iste natus error sitvolasuptate masease accusantium dolorem quelaudtium, totam rem aperiam.</p></div>
  <footer class="footer"><span class="footer-url"><svg viewBox="0 0 12 12"><circle cx="6" cy="6" r="5" fill="none" stroke="#fff" stroke-width="1"/><path d="M1 6h10M6 1c2.5 3 2.5 7 0 10M6 1c-2.5 3-2.5 7 0 10" fill="none" stroke="#fff" stroke-width=".8"/></svg>www.quelbrion.com</span><span class="footer-copy">© 2024. ALL Rights Reserved.</span><span class="footer-page">Page 06</span></footer>
</section>

<!-- Section divider -->
<section class="slide c1 r3">
  <div class="divider-photo" role="img" aria-label="Photo of a jet engine in a hangar lit with deep blue light"></div>
  <h2 class="divider-title">Caseo Oasemsna</h2>
  <p class="divider-sub">Werspiciatis aseeunde omnis iste natus error sitvolasuptate masease.</p>
</section>

<!-- Bullet list -->
<section class="slide c2 r3">
  <div class="brand brand-corner">Quelbrion</div>
  <h2 class="title title-center" style="top:15px">Kcas saeicas sesaec</h2>
  <ul class="bullets bullets-wide">
    <li>Harspiciatis unde omnis iste natus error sit voluptatem accusantium doloremque laudantium, totam rem aperiam, eaque ipsa quae ab illo inventore veritatis et quasi architecto beatae vitae dicta sunt explicabo. Nemo enim ipsam voluptatem quia voluptas sitsesae aspernatur aut odit</li>
    <li>Harspiciatis unde omnis iste natus error sit voluptatem accusantium doloremque laudantium, totam rem aperiam, eaque ipsa quae ab illo inventore veritatis et quasi architecto beatae vitae dicta sunt explicabo. Nemo enim ipsam voluptatem quia voluptas sitsesae aspernatur aut odit</li>
    <li>Harspiciatis unde omnis iste natus error sit voluptatem accusantium doloremque laudantium, totam rem aperiam, eaque ipsa quae ab illo inventore veritatis et quasi architecto beatae vitae dicta sunt explicabo. Nemo enim ipsam voluptatem quia voluptas sitsesae aspernatur aut odit</li>
    <li>Harspiciatis unde omnis iste natus error sit voluptatem accusantium doloremque laudantium, totam rem aperiam, eaque ipsa quae ab illo inventore veritatis et quasi architecto beatae vitae dicta sunt explicabo. Nemo enim ipsam voluptatem quia voluptas sitsesae aspernatur aut odit</li>
    <li>Harspiciatis unde omnis iste natus error sit voluptatem accusantium doloremque laudantium, totam rem aperiam, eaque ipsa quae ab illo inventore veritatis et quasi architecto beatae vitae dicta sunt explicabo. Nemo enim ipsam voluptatem quia voluptas sitsesae aspernatur aut odit</li>
  </ul>
  <footer class="footer"><span class="footer-url"><svg viewBox="0 0 12 12"><circle cx="6" cy="6" r="5" fill="none" stroke="#fff" stroke-width="1"/><path d="M1 6h10M6 1c2.5 3 2.5 7 0 10M6 1c-2.5 3-2.5 7 0 10" fill="none" stroke="#fff" stroke-width=".8"/></svg>www.quelbrion.com</span><span class="footer-copy">© 2024. ALL Rights Reserved.</span><span class="footer-page">Page 06</span></footer>
</section>

<!-- Two column bullets -->
<section class="slide c3 r3">
  <div class="brand brand-corner">Quelbrion</div>
  <h2 class="title title-center" style="top:15px">Kcas saeicas sesaec</h2>
  <ul class="bullets bullets-left">
    <li>Iasrspiciatis unde omnis iste natus error sit voluptatem accusantium doloremque laudantium, totam rem aperiam, eaque ipsa quae seab illo inventore veritatis et quasi architecto beatae vitae dicta ssaeunt explicabo. Nemo enim ipsam voluptatem quia voluptas sasffft ftsit aspernatur aut odit aut fugit, sed quia consequuntur magni dolores eos qui ratione voluptatem sequi nesciunt. Neque porro quisquam est, qui dolorem ipsum quia dolor sit amet, consectetur, afddipisci velit, sed quia non numquam eius modi tempora incidunt ut labore etasesese dolore magnam</li>
    <li>Harspiciatis unde omnis istae natus error sisaesesaet voluptatem accusantium doloremque laudantium, totam remssesese aperiam, eaque ipsaesesa qe aseab illo inventore veritatis saeset saequasi architecto beatae vitae.</li>
    <li>Uasesomnis istae natus error sisaesesaet voluptatem accusantium doloremque laudantium, totsdseam remssesese aperiam, eaque ipsaesesa qsaesee aseeab illso inventore veritatis saeset saequasi architecto beatae vitae.</li>
  </ul>
  <span class="col-rule"></span>
  <ul class="bullets bullets-right">
    <li>Harspiciatis unde omnis iste natus error sit voluptatem accusantium doloremque laudantium, totam remssesese aperiam, eaque ipsa quae ab illo inventore veritatis saeset saequasi architecto beatae vitae.</li>
    <li>Harspiciatis unde omnis iste natus error sit voluptatem accusantium doloremque laudantium, totam remssesese aperiam, eaque ipsa quae ab illo inventore veritatis saeset saequasi architecto beatae vitae.</li>
    <li>Harspiciatis unde omnis iste natus error sit voluptatem accusantium doloremque laudantium, totam remssesese aperiam, eaque ipsa quae ab illo inventore veritatis saeset saequasi architecto beatae vitae.</li>
    <li>Harspiciatis unde omnis iste natus error sit voluptatem accusantium doloremque laudantium, totam remssesese aperiam, eaque ipsa quae ab illo inventore veritatis saeset saequasi architecto beatae vitae.</li>
  </ul>
  <footer class="footer"><span class="footer-url"><svg viewBox="0 0 12 12"><circle cx="6" cy="6" r="5" fill="none" stroke="#fff" stroke-width="1"/><path d="M1 6h10M6 1c2.5 3 2.5 7 0 10M6 1c-2.5 3-2.5 7 0 10" fill="none" stroke="#fff" stroke-width=".8"/></svg>www.quelbrion.com</span><span class="footer-copy">© 2024. ALL Rights Reserved.</span><span class="footer-page">Page 06</span></footer>
</section>

</body>
</html>
```